professional business card design for technology company

We are a small technology consulting firm, specialising in consulting based around Cloud and Managed services. Our colour scheme is yellow, blue and white, as you can see in the logos. Although we are based in melbourne australia, due to the nature of our work, our clients can be located anywhere. We are looking for a clean, professional, positive look - similar to our company logo

Target Market(s)

small business

Industry/Entity Type

Business

Contact Information for Business Card

eye catching, designed to incorporate some level of raised printing. Must contain website address, phone number, name and job title

Requirements
Must have
• Logo (attached) - use of the same colour scheme

```html
<!DOCTYPE html>
<html lang="en">
<head>
<meta charset="utf-8">
<title>Cloudvane Business Card</title>
<link href="https://fonts.googleapis.com/css2?family=Open+Sans:wght@400;700;800&display=swap" rel="stylesheet">
<style>
  :root {
    --bg: #e9e6e1;
    --card: #ffffff;
    --blue: #35a9e1;
    --charcoal: #5a5b5d;
    --text: #333333;
  }
  html, body {
    margin: 0;
    padding: 0;
    width: 1200px;
    height: 1020px;
    overflow: hidden;
    background: var(--bg);
    font-family: "Open Sans", Arial, sans-serif;
  }
  .card {
    position: absolute;
    left: 100px;
    top: 224px;
    width: 1000px;
    height: 572px;
    background: var(--card);
    box-shadow: 0 10px 30px rgba(0,0,0,0.18);
    overflow: hidden;
  }
  .card-shapes {
    position: absolute;
    inset: 0;
  }
  .holder {
    position: absolute;
    left: 48px;
    top: 218px;
    color: #fff;
  }
  .holder-name {
    margin: 0;
    font-size: 36px;
    font-weight: 800;
    letter-spacing: 0.5px;
    line-height: 1.1;
  }
  .holder-title {
    margin: 4px 0 0;
    font-size: 21px;
    font-weight: 400;
    letter-spacing: 0.5px;
  }
  .brand {
    position: absolute;
    left: 560px;
    top: 150px;
    display: flex;
    align-items: center;
    gap: 18px;
  }
  .brand-dot {
    width: 46px;
    height: 46px;
    border-radius: 50%;
    background: var(--blue);
  }
  .brand-name {
    font-size: 64px;
    font-weight: 800;
    color: var(--charcoal);
    letter-spacing: -1px;
  }
  .contacts {
    position: absolute;
    left: 40px;
    top: 392px;
    margin: 0;
    padding: 0;
    list-style: none;
  }
  .contacts li {
    display: flex;
    align-items: center;
    height: 40px;
    font-size: 16px;
    color: var(--text);
  }
  .contact-icon {
    width: 36px;
    height: 20px;
    background: var(--blue);
    margin-right: 18px;
    display: flex;
    align-items: center;
    justify-content: center;
  }
</style>
</head>
<body>
  <div class="card">
    <svg class="card-shapes" width="1000" height="572" viewBox="0 0 1000 572" aria-hidden="true">
      <defs>
        <linearGradient id="under-sweep" x1="0" y1="0" x2="0" y2="1">
          <stop offset="0" stop-color="#e4e4e4"/>
          <stop offset="1" stop-color="#ffffff"/>
        </linearGradient>
        <linearGradient id="edge-sweep" x1="0" y1="0" x2="1" y2="0">
          <stop offset="0" stop-color="#f4f4f4"/>
          <stop offset="1" stop-color="#c4c4c4"/>
        </linearGradient>
      </defs>
      <path class="edge-sweep" d="M1000 0 V572 H860 C820 420 860 170 1000 40 Z" fill="url(#edge-sweep)"/>
      <path class="under-sweep" d="M0 372 C320 372 400 330 430 230 C452 150 470 40 560 0 H600 C500 50 490 170 470 250 C440 370 340 410 0 410 Z" fill="url(#under-sweep)"/>
      <path class="curve-line" d="M0 366 C320 366 390 325 418 230 C440 150 450 40 540 0 H562 C475 40 462 150 440 236 C412 345 330 382 0 382 Z" fill="var(--charcoal)"/>
      <path class="blue-band" d="M0 0 H530 C440 40 430 150 408 228 C380 322 320 358 0 358 Z" fill="var(--blue)"/>
    </svg>

    <div class="holder">
      <h1 class="holder-name">MARCUS HALE</h1>
      <p class="holder-title">GENERAL MANAGER</p>
    </div>

    <div class="brand">
      <span class="brand-dot"></span>
      <span class="brand-name">Cloudvane</span>
    </div>

    <ul class="contacts">
      <li>
        <span class="contact-icon">
          <svg width="12" height="12" viewBox="0 0 12 12"><path d="M2 1 L4.5 1 L5.5 3.5 L4 4.6 C4.7 6 6 7.3 7.4 8 L8.5 6.5 L11 7.5 L11 10 C6 10.5 1.5 6 2 1 Z" fill="#fff"/></svg>
        </span>
        041 287 5530
      </li>
      <li>
        <span class="contact-icon">
          <svg width="14" height="10" viewBox="0 0 14 10"><rect x="0.5" y="0.5" width="13" height="9" fill="none" stroke="#fff"/><path d="M0.5 0.5 L7 5.5 L13.5 0.5" fill="none" stroke="#fff"/></svg>
        </span>
        hello@cloudvane.io
      </li>
      <li>
        <span class="contact-icon">
          <svg width="12" height="12" viewBox="0 0 12 12"><circle cx="6" cy="6" r="5" fill="none" stroke="#fff" stroke-width="1.2"/><path d="M1 6 H11 M6 1 C3.5 3.5 3.5 8.5 6 11 C8.5 8.5 8.5 3.5 6 1" fill="none" stroke="#fff"/></svg>
        </span>
        www.cloudvane.io
      </li>
      <li>
        <span class="contact-icon">
          <svg width="10" height="13" viewBox="0 0 10 13"><path d="M5 12.5 C1.5 8 0.5 6.5 0.5 4.5 A4.5 4.5 0 0 1 9.5 4.5 C9.5 6.5 8.5 8 5 12.5 Z" fill="#fff"/><circle cx="5" cy="4.5" r="1.6" fill="var(--blue)"/></svg>
        </span>
        214, 9th floor, Harbour Line Road VIC
      </li>
    </ul>
  </div>
</body>
</html>
```